Business Card for Coastal Tundrabridge Advisory

We need a business card for Coastal Tundrabridge Advisory. The company website address is provided below. The company logo is attached. We provide specialized permafrost services to the mining, transportation, and oil & gas industries. The card should be prepared for:
Matthias Korhonen, PhD.
Coastal Tundrabridge Advisory
PO Box 418259
Quillwater, Alaska 99642
Direct: +1-907-555-0143
Email: mkorhonen@tundrabridgeadvisory.example
Website: www.coastaltundrabridgeadvisory.example

```html
<!DOCTYPE html>
<html lang="en">
<head>
<meta charset="utf-8">
<title>Coastal Tundrabridge Advisory – Business Card</title>
<link rel="stylesheet" href="https://fonts.googleapis.com/css2?family=Arimo:wght@400;600;700&display=swap">
<style>
  :root {
    --backdrop: #e3e3e3;
    --card-light: #f6f6f6;
    --card-dark: #0f1720;
    --ink: #121a23;
    --ink-soft: #4a4f55;
    --paper-text: #ffffff;
  }
  * { box-sizing: border-box; margin: 0; padding: 0; }
  html, body {
    width: 1200px; height: 1040px; overflow: hidden;
    background: var(--backdrop);
    font-family: "Arimo", Arial, sans-serif;
    color: var(--ink);
  }
  .canvas { position: relative; width: 1200px; height: 1040px; }
  .card {
    position: absolute; left: 282px; width: 644px; height: 366px;
    border-radius: 16px;
  }
  .card--front { top: 130px; background: var(--card-light); }
  .card--back { top: 568px; background: var(--card-dark); }

  .front__brand {
    position: absolute; right: 44px; top: 42px;
    text-align: right; font-weight: 600; color: var(--ink);
    text-transform: uppercase;
  }
  .front__brand-name { font-size: 19px; letter-spacing: 1.5px; line-height: 22px; display: block; }
  .front__brand-sub { font-size: 10px; letter-spacing: 3.2px; line-height: 14px; display: block; }

  .holder { position: absolute; left: 43px; top: 206px; }
  .holder__name { font-size: 23px; font-weight: 700; line-height: 28px; }
  .holder__degree { font-size: 18px; }
  .holder__title { font-size: 15.5px; color: var(--ink-soft); margin-left: 2px; line-height: 20px; }

  .divider {
    position: absolute; left: 43px; right: 44px; top: 256px;
    border-top: 1px solid var(--ink);
  }
  .contact {
    position: absolute; left: 43px; top: 262px; list-style: none;
    font-size: 15.5px; line-height: 20px;
  }
  .contact__item { display: flex; align-items: center; gap: 8px; }
  .contact__icon { width: 14px; height: 14px; flex: none; }
  .address {
    position: absolute; right: 44px; top: 262px;
    text-align: right; font-size: 15.5px; line-height: 20px; font-style: normal;
  }

  .back__brand {
    position: absolute; left: 0; right: 0; top: 138px;
    text-align: center; color: var(--paper-text); font-weight: 600;
    text-transform: uppercase;
  }
  .back__brand-name { display: block; font-size: 38px; letter-spacing: 2px; line-height: 46px; }
  .back__brand-sub { display: block; font-size: 17px; letter-spacing: 9px; line-height: 30px; }
</style>
</head>
<body>
<main class="canvas">
  <section class="card card--front" aria-label="Card front">
    <div class="front__brand">
      <span class="front__brand-name">Coastal Tundrabridge</span>
      <span class="front__brand-sub">Advisory</span>
    </div>

    <div class="holder">
      <p class="holder__name">Matthias Korhonen, <span class="holder__degree">PhD.</span></p>
      <p class="holder__title">President</p>
    </div>

    <div class="divider"></div>

    <ul class="contact">
      <li class="contact__item">
        <svg class="contact__icon" viewBox="0 0 16 16" aria-hidden="true"><path fill="#121a23" d="M3.6 1.2l2.3 2.6-1.2 2a9 9 0 0 0 5.5 5.5l2-1.2 2.6 2.3-1.2 2.2C8 15.8.2 8 .9 2.4z"/></svg>
        <span>+1-907-555-0143</span>
      </li>
      <li class="contact__item">
        <svg class="contact__icon" viewBox="0 0 16 16" aria-hidden="true"><rect x="1" y="4" width="14" height="9" fill="#121a23"/><path d="M1.5 4.5L8 9.5l6.5-5" stroke="#f6f6f6" stroke-width="1.3" fill="none"/></svg>
        <span>mkorhonen@tundrabridgeadvisory.example</span>
      </li>
      <li class="contact__item">
        <svg class="contact__icon" viewBox="0 0 16 16" aria-hidden="true"><circle cx="8" cy="8" r="7" fill="#121a23"/><path d="M4 5.5l3 1-1 3 2 1-1 3M10 3l1.5 2-1 2 2.5 1" stroke="#f6f6f6" stroke-width="1.2" fill="none"/></svg>
        <span>www.coastaltundrabridgeadvisory.example</span>
      </li>
    </ul>

    <address class="address">
      PO Box 418259<br>
      Quillwater, Alaska 99642
    </address>
  </section>

  <section class="card card--back" aria-label="Card back">
    <div class="back__brand">
      <span class="back__brand-name">Coastal Tundrabridge</span>
      <span class="back__brand-sub">Advisory</span>
    </div>
  </section>
</main>
</body>
</html>
```